Business Card Design for Training Business

Clear Path Coaching is a new business that delivers training and other services with a focus on topics related to mental health and wellbeing, for example, Wellmind Response Course, Resilience etc. We have a strong focus on evidence-based psychology and neuroscience. I have a logo which I will upload with the brief, so please consider colours that work well with the logo.
Target Market(s)
Adults, workplaces (particularly government and not-for-profits)
Industry/Entity Type
Business
Contact Information for Business Card
Head Strong TrainingSamantha SellwoodDirector0438 770 850sam@headstrongtraining.com.auwww.headstrongtraining.com.au

```html
<!DOCTYPE html>
<html lang="en">
<head>
<meta charset="utf-8">
<title>Clear Path Coaching – Business Card</title>
<link rel="stylesheet" href="https://fonts.googleapis.com/css2?family=Questrial&display=swap">
<style>
  :root {
    --backdrop: #3b3b3b;
    --card: #fbfbfb;
    --teal: #22b8bf;
    --teal-light: #2cc2c7;
    --ink: #ffffff;
    --grey-text: #555a5c;
  }
  * { margin: 0; padding: 0; box-sizing: border-box; }
  html, body {
    width: 1200px; height: 750px; overflow: hidden;
    background: var(--backdrop);
    font-family: "Questrial", sans-serif;
  }
  .canvas { position: relative; width: 1200px; height: 750px; }
  .card {
    position: absolute; left: 371px; width: 461px; height: 262px;
    background: var(--card); border-radius: 11px; overflow: hidden;
    box-shadow: 0 3px 6px rgba(0,0,0,0.35);
  }
  .card--front { top: 106px; }
  .card--back { top: 387px; }

  .contact-disc {
    position: absolute; left: -23px; top: -94px; width: 296px; height: 296px;
    border-radius: 50%;
    background: linear-gradient(160deg, var(--teal) 0%, var(--teal-light) 100%);
    box-shadow: 0 0 0 3px var(--card), 0 0 0 5.5px var(--teal);
  }
  .contact-block { position: absolute; left: 22px; top: 22px; color: var(--ink); }
  .contact-block__name { font-size: 19px; letter-spacing: 0.3px; line-height: 1; }
  .contact-block__role { font-size: 14px; line-height: 1; margin-top: 3px; }
  .contact-list { list-style: none; margin-top: 11px; }
  .contact-list li {
    display: flex; align-items: center; gap: 7px;
    font-size: 11.5px; line-height: 17.5px; letter-spacing: 0.1px;
  }
  .contact-list svg { width: 12px; height: 12px; flex: none; margin-left: 2px; }

  .brand {
    position: absolute; left: 262px; top: 128px; width: 182px;
    text-align: center; color: var(--grey-text);
  }
  .brand__mark {
    display: block; width: 64px; height: 64px; margin: 0 auto 14px;
    border: 1.5px solid var(--teal); border-radius: 50%;
  }
  .brand__name { font-size: 19px; letter-spacing: 2.6px; line-height: 1; }
  .brand__sub { font-size: 10px; letter-spacing: 4.5px; line-height: 1; margin-top: 8px; }

  .back-mark {
    position: absolute; left: 233px; top: 77px; width: 110px; height: 110px;
    transform: translateX(-50%); left: 230px;
    border: 1.5px solid var(--teal); border-radius: 50%;
  }
  .back-url {
    position: absolute; left: 0; right: 0; top: 228px;
    text-align: center; font-size: 12px; color: var(--grey-text);
  }
</style>
</head>
<body>
<main class="canvas">
  <section class="card card--front" aria-label="Business card front">
    <div class="contact-disc"></div>
    <div class="contact-block">
      <p class="contact-block__name">Rebecca Tanfield</p>
      <p class="contact-block__role">Director</p>
      <ul class="contact-list">
        <li>
          <svg viewBox="0 0 24 24" aria-hidden="true"><path fill="#fff" d="M6.6 10.8a15.1 15.1 0 0 0 6.6 6.6l2.2-2.2a1 1 0 0 1 1-.25 11.4 11.4 0 0 0 3.6.57 1 1 0 0 1 1 1V20a1 1 0 0 1-1 1A17 17 0 0 1 3 4a1 1 0 0 1 1-1h3.5a1 1 0 0 1 1 1c0 1.25.2 2.45.57 3.57a1 1 0 0 1-.25 1z"/></svg>
          0491 362 517
        </li>
        <li>
          <svg viewBox="0 0 24 24" aria-hidden="true"><rect x="2" y="5" width="20" height="14" fill="#fff"/><path d="M2 5l10 8 10-8" fill="none" stroke="#22b8bf" stroke-width="1.8"/></svg>
          bec@clearpathcoaching.example.au
        </li>
        <li>
          <svg viewBox="0 0 24 24" aria-hidden="true"><circle cx="12" cy="12" r="10" fill="#fff"/><path d="M7 8c2 0 3 1 3 3s-2 2-2 4M14 5c0 2 2 2 3 3s0 3 2 4M13 19c0-2 1-3 3-3" fill="none" stroke="#22b8bf" stroke-width="1.8"/></svg>
          www.clearpathcoaching.example.au
        </li>
      </ul>
    </div>
    <div class="brand">
      <span class="brand__mark"></span>
      <p class="brand__name">CLEAR PATH</p>
      <p class="brand__sub">COACHING</p>
    </div>
  </section>

  <section class="card card--back" aria-label="Business card back">
    <span class="back-mark"></span>
    <p class="back-url">www.clearpathcoaching.example.au</p>
  </section>
</main>
</body>
</html>
```